Fun A1 2012 family planner using clever typography and block colour

I have been looking for an A1 2012 family planner and I have not been able to find one. Hence I would like help to develop such a planner. I plan to print it on matt paper, portrait orientated. I have attached some reference pictures of our 2011 planner. I like interesting typography, clear clean colours and simple illustration. I need space to write in daily events and need the weeks and days to be clearly delineated from each other. Each day cell needs the date and day in it (please refer to the file uploaded for a visual reference confirming this). Each weekend needs some kind of colour/ typographic delineation. I want a design for a year-at-a-view calendar. I plan to print the planner in Sydney, Australia with brightloomprints.com.au and probably to sell printed copies online. The terms & conditions of this project are that I will own the design concept 100% and in perpetuity worldwide once payment has been made. (NB. The attached Work File in Word contains a rough layout and all months, days and dates all typed up to make for quicker design.)

Target Market(s)

Reasonably well heeled family of 4. 2 parents. 2 kids. 2 pets.

Industry/Entity Type

Events

Requirements
Must have
• The calendar must be portrait (not landscape orientated), A1 size. It will be printed on matt paper by brightloomprints.com.au. It must have months running left to right (Jan-Dec) and day/date cells running top to bottom (refer 2011 planner photos in file uploaded). The day/ date cells must be around 3(w)x2(h)cm - big enough to write daily events in. Weekends must be colour/ typographically delineated. 2012 year must be noted as must "A Pebblegate Inc Project" and web address in fine print bottom left hand left hand corner.
Nice to have
• A Pebblegate Inc logo in bottom left hand corder (perhaps Nimble Owl like: http://www.artmarketly.com/design_submission.aspx?designid=731462). Header/Footer space for customisation (e.g. "Hartono-Quist 2012 Planner" or "XYZ Co 2012 Planner".
Should not have
• The calendar should not use photographs or resemble standard or cheesy wall calendars. No watermarks please.

```html
<!DOCTYPE html>
<html lang="en">
<head>
<meta charset="utf-8">
<title>XYZ Co 2012 Planner</title>
<link rel="stylesheet" href="https://fonts.googleapis.com/css2?family=Signika:wght@400;600;700&display=swap">
<style>
:root{
  --orange:#f7941d; --blue:#00aeef; --pink:#ea5fa3; --red:#e31e26; --green:#72b843; --purple:#9b4f9e;
  --text:#6b6b6b; --footer:#bdbdbd;
  --col-w:62.5px; --gap:3.1px;
}
*{box-sizing:border-box;margin:0;padding:0}
html,body{width:847px;height:1200px;overflow:hidden;background:#fff}
body{position:relative;font-family:"Signika",sans-serif}
.months,.days{position:absolute;left:30px;display:grid;grid-template-columns:repeat(12,var(--col-w));column-gap:var(--gap)}
.months{top:0;height:89px}
.month{background:var(--c);border-radius:0 0 6px 6px;color:#fff;font-weight:700;font-size:27px;letter-spacing:-.5px;
  display:flex;align-items:flex-end;justify-content:center;padding-bottom:17px;text-shadow:0 1px 2px rgba(0,0,0,.25)}
.days{top:99px;grid-auto-rows:31px;row-gap:2.5px}
.days p{background:var(--tint);border-radius:3px;padding:3px 4px 0;font-size:7.5px;line-height:1;color:var(--text)}
.days p b{display:block;font-size:14px;font-weight:400;line-height:1.05;margin-bottom:1px}
.days p.h{background:var(--hl);color:var(--ink)}
.months .month:nth-child(6n+1),.days p:nth-child(6n+1){--c:var(--orange)}
.months .month:nth-child(6n+2),.days p:nth-child(6n+2){--c:var(--blue)}
.months .month:nth-child(6n+3),.days p:nth-child(6n+3){--c:var(--pink)}
.months .month:nth-child(6n+4),.days p:nth-child(6n+4){--c:var(--red)}
.months .month:nth-child(6n+5),.days p:nth-child(6n+5){--c:var(--green)}
.months .month:nth-child(6n){--c:var(--purple)}
.days p:nth-child(12n+1){--tint:#fffad0;--hl:#fff385;--ink:#f39a1e}
.days p:nth-child(12n+2){--tint:#e8f5fc;--hl:#b6e3f8;--ink:#1aa6df}
.days p:nth-child(12n+3){--tint:#fdf0f6;--hl:#f9d0e3;--ink:#e0559a}
.days p:nth-child(12n+4){--tint:#fdebd9;--hl:#fdd4ae;--ink:#e3282b}
.days p:nth-child(12n+5){--tint:#eff6e7;--hl:#d6e9c4;--ink:#5ea633}
.days p:nth-child(12n+6){--tint:#f6f2f7;--hl:#e8dcec;--ink:#9b4f9e}
.days p:nth-child(12n+7){--tint:#fffad0;--hl:#fff385;--ink:#f39a1e}
.days p:nth-child(12n+8){--tint:#e8f5fc;--hl:#b6e3f8;--ink:#1aa6df}
.days p:nth-child(12n+9){--tint:#fdf0f6;--hl:#f9d0e3;--ink:#e0559a}
.days p:nth-child(12n+10){--tint:#fdebd9;--hl:#fdd4ae;--ink:#e3282b}
.days p:nth-child(12n+11){--tint:#eff6e7;--hl:#d6e9c4;--ink:#5ea633}
.days p:nth-child(12n){--tint:#f6f2f7;--hl:#e8dcec;--ink:#9b4f9e}
.planner-title{position:absolute;left:30px;top:1146px;font-size:28px;font-weight:600;color:var(--footer);letter-spacing:.2px}
</style>
</head>
<body>
<header class="months">
  <div class="month">JAN</div><div class="month">FEB</div><div class="month">MAR</div><div class="month">APR</div>
  <div class="month">MAY</div><div class="month">JUN</div><div class="month">JUL</div><div class="month">AUG</div>
  <div class="month">SEP</div><div class="month">OCT</div><div class="month">NOV</div><div class="month">DEC</div>
</header>
<main class="days">
<!-- row 1 -->
<p class="h"><b>01</b>Sun</p><p><b>01</b>Wed</p><p><b>01</b>Thu</p><p><b>01</b>Sun</p><p><b>01</b>Tue</p><p><b>01</b>Fri</p><p class="h"><b>01</b>Sun</p><p><b>01</b>Wed</p><p class="h"><b>01</b>Sat</p><p><b>01</b>Mon</p><p><b>01</b>Thu</p><p class="h"><b>01</b>Sat</p>
<!-- row 2 -->
<p><b>02</b>Mon</p><p><b>02</b>Thu</p><p><b>02</b>Fri</p><p><b>02</b>Mon</p><p><b>02</b>Wed</p><p class="h"><b>02</b>Sat</p><p><b>02</b>Mon</p><p><b>02</b>Thu</p><p class="h"><b>02</b>Sun</p><p><b>02</b>Tue</p><p><b>02</b>Fri</p><p class="h"><b>02</b>Sun</p>
<!-- row 3 -->
<p><b>03</b>Tue</p><p><b>01</b>Wed</p><p class="h"><b>01</b>Thu</p><p><b>01</b>Sun</p><p><b>01</b>Tue</p><p class="h"><b>01</b>Fri</p><p><b>01</b>Sun</p><p><b>01</b>Wed</p><p><b>01</b>Sat</p><p><b>01</b>Mon</p><p class="h"><b>01</b>Thu</p><p><b>01</b>Sat</p>
<!-- row 4 -->
<p><b>02</b>Thu</p><p class="h"><b>02</b>Thu</p><p class="h"><b>02</b>Fri</p><p><b>02</b>Mon</p><p><b>02</b>Wed</p><p><b>02</b>Sat</p><p><b>02</b>Mon</p><p class="h"><b>02</b>Thu</p><p><b>02</b>Sun</p><p><b>02</b>Tue</p><p class="h"><b>02</b>Fri</p><p><b>02</b>Sun</p>
<!-- row 5 -->
<p><b>05</b>Thu</p><p class="h"><b>01</b>Wed</p><p><b>01</b>Thu</p><p><b>01</b>Sun</p><p class="h"><b>01</b>Tue</p><p><b>01</b>Fri</p><p><b>01</b>Sun</p><p class="h"><b>01</b>Wed</p><p><b>01</b>Sat</p><p><b>01</b>Mon</p><p><b>01</b>Thu</p><p><b>01</b>Sat</p>
<!-- row 6 -->
<p><b>06</b>Fri</p><p><b>02</b>Thu</p><p><b>02</b>Fri</p><p><b>02</b>Mon</p><p class="h"><b>02</b>Wed</p><p><b>02</b>Sat</p><p><b>02</b>Mon</p><p><b>02</b>Thu</p><p><b>02</b>Sun</p><p class="h"><b>02</b>Tue</p><p><b>02</b>Fri</p><p><b>02</b>Sun</p>
<!-- row 7 -->
<p class="h"><b>07</b>Sat</p><p><b>01</b>Wed</p><p><b>01</b>Thu</p><p class="h"><b>01</b>Sun</p><p><b>01</b>Tue</p><p><b>01</b>Fri</p><p class="h"><b>01</b>Sun</p><p><b>01</b>Wed</p><p><b>01</b>Sat</p><p class="h"><b>01</b>Mon</p><p><b>01</b>Thu</p><p><b>01</b>Sat</p>
<!-- row 8 -->
<p class="h"><b>08</b>Sun</p><p><b>01</b>Wed</p><p><b>01</b>Thu</p><p class="h"><b>01</b>Sun</p><p><b>01</b>Tue</p><p><b>01</b>Fri</p><p class="h"><b>01</b>Sun</p><p><b>01</b>Wed</p><p class="h"><b>01</b>Sat</p><p><b>01</b>Mon</p><p><b>01</b>Thu</p><p class="h"><b>01</b>Sat</p>
<!-- row 9 -->
<p><b>09</b>Mon</p><p><b>02</b>Thu</p><p><b>02</b>Fri</p><p><b>02</b>Mon</p><p><b>02</b>Wed</p><p class="h"><b>02</b>Sat</p><p><b>02</b>Mon</p><p><b>02</b>Thu</p><p class="h"><b>02</b>Sun</p><p><b>02</b>Tue</p><p><b>02</b>Fri</p><p class="h"><b>02</b>Sun</p>
<!-- row 10 -->
<p><b>10</b>Tue</p><p><b>01</b>Wed</p><p class="h"><b>01</b>Thu</p><p><b>01</b>Sun</p><p><b>01</b>Tue</p><p class="h"><b>01</b>Fri</p><p><b>01</b>Sun</p><p><b>01</b>Wed</p><p><b>01</b>Sat</p><p><b>01</b>Mon</p><p class="h"><b>01</b>Thu</p><p><b>01</b>Sat</p>
<!-- row 11 -->
<p><b>02</b>Thu</p><p class="h"><b>02</b>Thu</p><p class="h"><b>02</b>Fri</p><p><b>02</b>Mon</p><p><b>02</b>Wed</p><p><b>02</b>Sat</p><p><b>02</b>Mon</p><p class="h"><b>02</b>Thu</p><p><b>02</b>Sun</p><p><b>02</b>Tue</p><p class="h"><b>02</b>Fri</p><p><b>02</b>Sun</p>
<!-- row 12 -->
<p><b>12</b>Thu</p><p class="h"><b>01</b>Wed</p><p><b>01</b>Thu</p><p><b>01</b>Sun</p><p class="h"><b>01</b>Tue</p><p><b>01</b>Fri</p><p><b>01</b>Sun</p><p class="h"><b>01</b>Wed</p><p><b>01</b>Sat</p><p><b>01</b>Mon</p><p><b>01</b>Thu</p><p><b>01</b>Sat</p>
<!-- row 13 -->
<p><b>13</b>Fri</p><p><b>02</b>Thu</p><p><b>02</b>Fri</p><p><b>02</b>Mon</p><p class="h"><b>02</b>Wed</p><p><b>02</b>Sat</p><p><b>02</b>Mon</p><p><b>02</b>Thu</p><p><b>02</b>Sun</p><p class="h"><b>02</b>Tue</p><p><b>02</b>Fri</p><p><b>02</b>Sun</p>
<!-- row 14 -->
<p class="h"><b>14</b>Sat</p><p><b>01</b>Wed</p><p><b>01</b>Thu</p><p class="h"><b>01</b>Sun</p><p><b>01</b>Tue</p><p><b>01</b>Fri</p><p class="h"><b>01</b>Sun</p><p><b>01</b>Wed</p><p><b>01</b>Sat</p><p class="h"><b>01</b>Mon</p><p><b>01</b>Thu</p><p><b>01</b>Sat</p>
<!-- row 15 -->
<p class="h"><b>15</b>Sun</p><p><b>01</b>Wed</p><p><b>01</b>Thu</p><p class="h"><b>01</b>Sun</p><p><b>01</b>Tue</p><p><b>01</b>Fri</p><p class="h"><b>01</b>Sun</p><p><b>01</b>Wed</p><p class="h"><b>01</b>Sat</p><p><b>01</b>Mon</p><p><b>01</b>Thu</p><p class="h"><b>01</b>Sat</p>
<!-- row 16 -->
<p><b>16</b>Mon</p><p><b>02</b>Thu</p><p><b>02</b>Fri</p><p><b>02</b>Mon</p><p><b>02</b>Wed</p><p class="h"><b>02</b>Sat</p><p><b>02</b>Mon</p><p><b>02</b>Thu</p><p class="h"><b>02</b>Sun</p><p><b>02</b>Tue</p><p><b>02</b>Fri</p><p class="h"><b>02</b>Sun</p>
<!-- row 17 -->
<p><b>17</b>Tue</p><p><b>01</b>Wed</p><p class="h"><b>01</b>Thu</p><p><b>01</b>Sun</p><p><b>01</b>Tue</p><p class="h"><b>01</b>Fri</p><p><b>01</b>Sun</p><p><b>01</b>Wed</p><p><b>01</b>Sat</p><p><b>01</b>Mon</p><p class="h"><b>01</b>Thu</p><p><b>01</b>Sat</p>
<!-- row 18 -->
<p><b>02</b>Thu</p><p class="h"><b>02</b>Thu</p><p class="h"><b>02</b>Fri</p><p><b>02</b>Mon</p><p><b>02</b>Wed</p><p><b>02</b>Sat</p><p><b>02</b>Mon</p><p class="h"><b>02</b>Thu</p><p><b>02</b>Sun</p><p><b>02</b>Tue</p><p class="h"><b>02</b>Fri</p><p><b>02</b>Sun</p>
<!-- row 19 -->
<p><b>19</b>Thu</p><p class="h"><b>01</b>Wed</p><p><b>01</b>Thu</p><p><b>01</b>Sun</p><p class="h"><b>01</b>Tue</p><p><b>01</b>Fri</p><p><b>01</b>Sun</p><p class="h"><b>01</b>Wed</p><p><b>01</b>Sat</p><p><b>01</b>Mon</p><p><b>01</b>Thu</p><p><b>01</b>Sat</p>
<!-- row 20 -->
<p><b>20</b>Fri</p><p><b>02</b>Thu</p><p><b>02</b>Fri</p><p><b>02</b>Mon</p><p class="h"><b>02</b>Wed</p><p><b>02</b>Sat</p><p><b>02</b>Mon</p><p><b>02</b>Thu</p><p><b>02</b>Sun</p><p class="h"><b>02</b>Tue</p><p><b>02</b>Fri</p><p><b>02</b>Sun</p>
<!-- row 21 -->
<p class="h"><b>21</b>Sat</p><p><b>01</b>Wed</p><p><b>01</b>Thu</p><p class="h"><b>01</b>Sun</p><p><b>01</b>Tue</p><p><b>01</b>Fri</p><p class="h"><b>01</b>Sun</p><p><b>01</b>Wed</p><p><b>01</b>Sat</p><p class="h"><b>01</b>Mon</p><p><b>01</b>Thu</p><p><b>01</b>Sat</p>
<!-- row 22 -->
<p class="h"><b>22</b>Sun</p><p><b>01</b>Wed</p><p><b>01</b>Thu</p><p class="h"><b>01</b>Sun</p><p><b>01</b>Tue</p><p><b>01</b>Fri</p><p class="h"><b>01</b>Sun</p><p><b>01</b>Wed</p><p class="h"><b>01</b>Sat</p><p><b>01</b>Mon</p><p><b>01</b>Thu</p><p class="h"><b>01</b>Sat</p>
<!-- row 23 -->
<p><b>23</b>Mon</p><p><b>02</b>Thu</p><p><b>02</b>Fri</p><p><b>02</b>Mon</p><p><b>02</b>Wed</p><p class="h"><b>02</b>Sat</p><p><b>02</b>Mon</p><p><b>02</b>Thu</p><p class="h"><b>02</b>Sun</p><p><b>02</b>Tue</p><p><b>02</b>Fri</p><p class="h"><b>02</b>Sun</p>
<!-- row 24 -->
<p><b>24</b>Tue</p><p><b>01</b>Wed</p><p class="h"><b>01</b>Thu</p><p><b>01</b>Sun</p><p><b>01</b>Tue</p><p class="h"><b>01</b>Fri</p><p><b>01</b>Sun</p><p><b>01</b>Wed</p><p><b>01</b>Sat</p><p><b>01</b>Mon</p><p class="h"><b>01</b>Thu</p><p><b>01</b>Sat</p>
<!-- row 25 -->
<p><b>02</b>Thu</p><p class="h"><b>02</b>Thu</p><p class="h"><b>02</b>Fri</p><p><b>02</b>Mon</p><p><b>02</b>Wed</p><p><b>02</b>Sat</p><p><b>02</b>Mon</p><p class="h"><b>02</b>Thu</p><p><b>02</b>Sun</p><p><b>02</b>Tue</p><p class="h"><b>02</b>Fri</p><p><b>02</b>Sun</p>
<!-- row 26 -->
<p><b>26</b>Thu</p><p class="h"><b>01</b>Wed</p><p><b>01</b>Thu</p><p><b>01</b>Sun</p><p class="h"><b>01</b>Tue</p><p><b>01</b>Fri</p><p><b>01</b>Sun</p><p class="h"><b>01</b>Wed</p><p><b>01</b>Sat</p><p><b>01</b>Mon</p><p><b>01</b>Thu</p><p><b>01</b>Sat</p>
<!-- row 27 -->
<p><b>27</b>Fri</p><p><b>02</b>Thu</p><p><b>02</b>Fri</p><p><b>02</b>Mon</p><p class="h"><b>02</b>Wed</p><p><b>02</b>Sat</p><p><b>02</b>Mon</p><p><b>02</b>Thu</p><p><b>02</b>Sun</p><p class="h"><b>02</b>Tue</p><p><b>02</b>Fri</p><p><b>02</b>Sun</p>
<!-- row 28 -->
<p class="h"><b>28</b>Sat</p><p><b>01</b>Wed</p><p><b>01</b>Thu</p><p class="h"><b>01</b>Sun</p><p><b>01</b>Tue</p><p><b>01</b>Fri</p><p class="h"><b>01</b>Sun</p><p><b>01</b>Wed</p><p><b>01</b>Sat</p><p class="h"><b>01</b>Mon</p><p><b>01</b>Thu</p><p><b>01</b>Sat</p>
<!-- row 29 -->
<p class="h"><b>29</b>Sun</p><p><b>01</b>Wed</p><p><b>01</b>Thu</p><p class="h"><b>01</b>Sun</p><p><b>01</b>Tue</p><p><b>01</b>Fri</p><p class="h"><b>01</b>Sun</p><p><b>01</b>Wed</p><p class="h"><b>01</b>Sat</p><p><b>01</b>Mon</p><p><b>01</b>Thu</p><p class="h"><b>01</b>Sat</p>
<!-- row 30 -->
<p><b>30</b>Mon</p><p><b>02</b>Thu</p><p><b>02</b>Fri</p><p><b>02</b>Mon</p><p><b>02</b>Wed</p><p class="h"><b>02</b>Sat</p><p><b>02</b>Mon</p><p><b>02</b>Thu</p><p class="h"><b>02</b>Sun</p><p><b>02</b>Tue</p><p><b>02</b>Fri</p><p class="h"><b>02</b>Sun</p>
<!-- row 31 -->
<p><b>31</b>Tue</p><p><b>01</b>Wed</p><p class="h"><b>01</b>Thu</p><p><b>01</b>Sun</p><p><b>01</b>Tue</p><p class="h"><b>01</b>Fri</p><p><b>01</b>Sun</p><p><b>01</b>Wed</p><p><b>01</b>Sat</p><p><b>01</b>Mon</p><p class="h"><b>01</b>Thu</p><p><b>01</b>Sat</p>
</main>
<footer class="planner-title">XYZ Co 2012 Planner</footer>
</body>
</html>
```